Indy Film Production Company/Studio

We need a business card designed from an existing logo. We are a digital studio/production company that caters to creating genre entertainment, like Action, Horror, and martial arts. The card along with the logo will be used to Brand the company from letter heads to banners. The design will also be used for postcards and Brochures. It should be professional and masculine.
Updates

Thank you to all the designers who have participated. I'm narrowing down who it will be. Thank you again.

Target Market(s)

Investors, Networks, Producers, and actors

Industry/Entity Type

Film Production

Contact Information for Business Card

Teodoro Valbuena
Producer/Writer/Director
www.kestrelpicturehouse.example

Requirements
Must have
• Website address, Facebook icon and Twitter icon possibly in the back of the card.
Nice to have
• Logline of Company: Follow The Action.

```html
<!DOCTYPE html>
<html lang="en">
<head>
<meta charset="utf-8">
<title>Kestrel Picture House – Business Card</title>
<link href="https://fonts.googleapis.com/css2?family=Roboto:ital,wght@0,400;0,700;1,700&display=swap" rel="stylesheet">
<style>
  :root {
    --backdrop: #a9a7a8;
    --brand-red: #cc2f2a;
    --card-dark: #2b2727;
    --ink-light: #f1efee;
    --band-grey: #c4c3c3;
    --rule: #d9d6d5;
  }
  * { margin: 0; padding: 0; box-sizing: border-box; }
  html, body {
    width: 1200px; height: 1200px; overflow: hidden;
    background: var(--backdrop);
    font-family: "Roboto", Arial, sans-serif;
  }
  .canvas { position: relative; width: 1200px; height: 1200px; }

  .card { position: absolute; overflow: hidden; width: 713px; height: 417px; left: 231px; }

  /* Front */
  .card-front { top: 118px; background: var(--brand-red); }
  .front-wordmark {
    position: absolute; left: 0; right: 0; top: 138px;
    color: var(--ink-light); text-align: center;
    font-weight: 700; font-size: 50px; line-height: 54px;
    letter-spacing: 1px; text-transform: uppercase;
  }
  .front-links {
    position: absolute; left: 0; right: 0; bottom: 34px;
    display: flex; justify-content: center; align-items: center; gap: 26px;
    color: var(--ink-light); font-size: 16px;
  }
  .front-links .link { display: flex; align-items: center; gap: 8px; }
  .social-dot { width: 14px; height: 14px; border-radius: 50%; background: var(--ink-light); }

  /* Back */
  .card-back { top: 644px; background: var(--card-dark); }
  .back-wordmark {
    position: absolute; left: 37px; top: 66px;
    color: var(--brand-red);
    font-weight: 700; font-size: 50px; line-height: 56px;
    letter-spacing: 1px; text-transform: uppercase;
  }
  .holder { position: absolute; right: 34px; top: 198px; text-align: right; }
  .holder-name {
    color: var(--brand-red); font-weight: 700; font-style: italic;
    font-size: 26px; line-height: 32px;
  }
  .holder-title { color: var(--ink-light); font-size: 16px; margin-top: 6px; }
  .divider {
    position: absolute; left: 37px; top: 255px; width: 482px; height: 1px;
    background: var(--rule);
  }
  .contact-list { position: absolute; left: 37px; top: 281px; list-style: none; }
  .contact-list li {
    display: flex; align-items: center; height: 27.5px;
    color: var(--ink-light); font-size: 17px;
  }
  .contact-list svg { width: 17px; height: 17px; margin-right: 18px; fill: var(--brand-red); flex: none; }
  .address {
    position: absolute; right: 34px; top: 293px; text-align: right;
    color: var(--ink-light); font-size: 17px; line-height: 28px;
  }
  .footer-bands { position: absolute; left: 0; bottom: 0; width: 713px; height: 42px; }
</style>
</head>
<body>
<main class="canvas">

  <section class="card card-front" aria-label="Card front">
    <div class="front-wordmark">Kestrel<br>Picture House</div>
    <div class="front-links">
      <span class="link">www.kestrelpicturehouse.example</span>
      <span class="link"><span class="social-dot"></span>/kestrelpicturehouse</span>
      <span class="link"><span class="social-dot"></span>@kestrelpictures</span>
    </div>
  </section>

  <section class="card card-back" aria-label="Card back">
    <div class="back-wordmark">Kestrel<br>Picture House</div>

    <div class="holder">
      <div class="holder-name">Teodoro Valbuena</div>
      <div class="holder-title">Producer/Writer/Director</div>
    </div>

    <div class="divider"></div>

    <ul class="contact-list">
      <li>
        <svg viewBox="0 0 24 24" aria-hidden="true"><path d="M6.6 10.8a15 15 0 0 0 6.6 6.6l2.2-2.2c.3-.3.7-.4 1-.2 1.1.4 2.3.6 3.6.6.6 0 1 .4 1 1V20c0 .6-.4 1-1 1A17 17 0 0 1 3 4c0-.6.4-1 1-1h3.5c.6 0 1 .4 1 1 0 1.3.2 2.5.6 3.6.1.3 0 .7-.2 1z"/></svg>
        5550148273
      </li>
      <li>
        <svg viewBox="0 0 24 24" aria-hidden="true"><path d="M12 2a10 10 0 1 0 0 20 10 10 0 0 0 0-20zm6.9 6h-2.9a15.6 15.6 0 0 0-1.4-3.6A8 8 0 0 1 18.9 8zM12 4c.8 1.2 1.5 2.5 1.9 4h-3.8c.4-1.5 1.1-2.8 1.9-4zM4.3 14a8 8 0 0 1 0-4h3.4a16 16 0 0 0 0 4zm.8 2h2.9c.3 1.3.8 2.5 1.4 3.6A8 8 0 0 1 5.1 16zM8 8H5.1a8 8 0 0 1 4.3-3.6C8.8 5.5 8.4 6.7 8 8zm4 12c-.8-1.2-1.5-2.5-1.9-4h3.8c-.4 1.5-1.1 2.8-1.9 4zm2.3-6H9.7a14.7 14.7 0 0 1 0-4h4.6a14.7 14.7 0 0 1 0 4zm.3 5.6c.6-1.1 1.1-2.3 1.4-3.6h2.9a8 8 0 0 1-4.3 3.6zm1.7-5.6a16 16 0 0 0 0-4h3.4a8 8 0 0 1 0 4z"/></svg>
        www.kestrelpicturehouse.example
      </li>
      <li>
        <svg viewBox="0 0 24 24" aria-hidden="true"><path d="M2 5h20v14H2zm2 2v.5l8 5 8-5V7zm0 2.8V17h16V9.8l-8 5z"/></svg>
        yourname@yourwebsite.com
      </li>
    </ul>

    <div class="address">Your Long Commercial or<br>business address in 2 line</div>

    <svg class="footer-bands" viewBox="0 0 713 42" aria-hidden="true">
      <rect x="0" y="21" width="390" height="21" fill="var(--brand-red)"/>
      <polygon points="394,0 713,0 713,42 374,42" fill="var(--band-grey)"/>
    </svg>
  </section>

</main>
</body>
</html>
```